bRIDGE ON LLC - New Website Design Help!

Need to build a website that showcases our capabilities. We will be specializing in Government Contracting for SDVOSB set aside and sole source contracts. We provide many services such as Audio & Visual design, install, consulting, all the way through to project completion. Also, IT/Voice infrastructure consulting, design, implementation, project management all the way to project completion.

Target Market(s)

IT/Voice Government Contracts, Managed Service Contracts for Government

Industry/Entity Type

Information Technology and Telecommunications

Coding

Coded - Design and coding required

Number of Pages Required

5+ page

Font styles to use
Other font styles liked:
• Calibri

Colors

Designer to choose only greyscale colors for use in the design.

Requirements
Must have
• Drop downs for additional pages, for About Us, Services, Industry Solutions, Our Company, Contact Us
Nice to have
• Testimonials page or Blog page

```html
<!DOCTYPE html>
<html lang="en">
<head>
<meta charset="utf-8">
<title>bRIDGE ON LLC</title>
<link href="https://fonts.googleapis.com/css2?family=Roboto:ital,wght@0,400;0,500;0,700;1,400&display=swap" rel="stylesheet">
<style>
:root{
  --black:#000;
  --ink:#1c1c1c;
  --text:#5a5a5a;
  --white:#fff;
  --light:#f3f3f3;
  --line:#9a9a9a;
  --photo-dark:#3a3d40;
}
*{box-sizing:border-box;margin:0;padding:0}
html,body{width:1200px;height:4049px;overflow:hidden}
body{position:relative;font-family:'Roboto',Arial,sans-serif;background:var(--white);color:var(--ink)}
.abs{position:absolute}
.photo{position:absolute}
.btn{position:absolute;display:flex;align-items:center;justify-content:center;font-size:12px;font-weight:700;letter-spacing:.3px}
.btn-light{background:var(--white);color:var(--black)}
.btn-dark{background:var(--black);color:var(--white)}
.wordmark{font-weight:700;letter-spacing:3px;color:var(--white);display:flex;align-items:center;gap:10px}
.wordmark .sq{width:14px;height:14px;background:var(--white)}
.section-title{position:absolute;font-weight:700;font-size:36px;text-transform:uppercase}
.round-arrow{position:absolute;border-radius:50%;display:flex;align-items:center;justify-content:center}

/* header + hero */
.hero{left:0;top:0;width:1200px;height:639px;background:linear-gradient(180deg,#5d6064 0%,#4a4c4f 50%,#3d3f42 100%)}
.topbar{left:0;top:0;width:1200px;height:79px;background:rgba(20,20,20,.75)}
.topbar .wordmark{position:absolute;left:144px;top:18px;height:38px;font-size:28px}
.nav{position:absolute;left:400px;top:34px;display:flex;gap:27px;font-size:13px;color:var(--white)}
.nav .active{position:relative}
.nav .active::before{content:"";position:absolute;left:0;top:-24px;width:36px;height:3px;background:var(--white)}
.hero-title{left:0;top:262px;width:1200px;text-align:center;font-size:96px;font-weight:700;color:var(--white);letter-spacing:-1px;line-height:1}
.hero-text{left:350px;top:376px;width:500px;text-align:center;font-size:13px;line-height:24px;color:var(--white)}
.hero .round-arrow{width:44px;height:44px;background:var(--black);top:340px}

/* about */
.about-band{left:0;top:639px;width:702px;height:449px;background:var(--black)}
.about-title{left:141px;top:728px;color:var(--white)}
.about-text{left:141px;top:778px;width:412px;font-size:13.5px;line-height:24px;color:var(--white);text-align:justify}

/* services */
.service{position:absolute;top:1304px;width:209px;height:177px;border:4px solid var(--black);display:flex;flex-direction:column;align-items:center;justify-content:flex-end;padding-bottom:26px;gap:22px;font-size:12px;font-weight:700;text-transform:uppercase}
.service svg{width:84px;height:84px}
.dark-arrow{width:44px;height:44px;background:var(--black);top:1378px}

/* industry */
.industry{left:0;top:1579px;width:1200px;height:516px;background:var(--light)}
.industry-text{left:600px;top:1720px;width:454px;font-size:13px;line-height:19.7px;color:var(--text);text-align:justify}

/* testimonials */
.testi-bg{left:0;top:2095px;width:1200px;height:536px;background:linear-gradient(180deg,#2c2d2f,#1b1c1d 60%,#2a2b2d)}
.card{position:absolute;top:2252px;width:437px;height:242px;border:2px solid var(--white);padding:26px 28px 0;color:var(--white)}
.card p{font-style:italic;font-size:13px;line-height:19.8px;text-align:justify}
.card .who{display:flex;align-items:center;gap:14px;margin-top:14px}
.card .avatar{width:66px;height:66px;border-radius:50%;background:linear-gradient(160deg,#d9d9d9,#8d8d8d)}
.card .name{font-size:20px;font-weight:500}
.card .co{font-size:12px;margin-top:6px}
.card .quote{position:absolute;right:26px;bottom:-24px;width:64px;height:48px;background:#1d1e1f}
.dots{left:570px;top:2544px;display:flex;gap:8px}
.dots span{width:10px;height:10px;border-radius:50%;background:#555}
.dots span:first-child{background:var(--white)}

/* company */
.company-text{left:245px;top:2775px;width:708px;text-align:justify;text-align-last:center;font-size:13px;line-height:20px;color:var(--text)}

/* contact */
.contact-bg{left:0;top:3028px;width:1200px;height:480px;background:linear-gradient(90deg,#7c7a75,#4f5a60 40%,#3e4a52 70%,#6b6a68)}
.footer-bg{left:0;top:3508px;width:1200px;height:541px;background:var(--black)}
.form-card{left:228px;top:3192px;width:744px;height:455px;background:var(--white)}
.field{position:absolute;border-bottom:1.5px solid var(--line);font-size:12px;color:#777;padding:0 0 8px 8px}

/* footer */
.footer-mark{left:0;top:3716px;width:1200px;justify-content:center;font-size:30px;display:flex}
.rule{left:144px;width:911px;height:1px;background:#555}
.foot-nav{left:0;top:3800px;width:1200px;display:flex;justify-content:center;gap:27px;font-size:12px;color:var(--white)}
.info{position:absolute;top:3880px;display:flex;gap:20px;color:var(--white)}
.info .ico{width:47px;height:46px;background:var(--white);display:flex;align-items:center;justify-content:center}
.info h4{font-size:14px;font-weight:700;margin-top:2px}
.info p{font-size:13px;line-height:24px;margin-top:4px}
.copy{left:0;top:3996px;width:1200px;text-align:center;font-size:12px;color:var(--white)}
</style>
</head>
<body>

<!-- Hero -->
<div class="photo hero" role="img" aria-label="Team of colleagues talking in a bright modern office"></div>
<div class="abs topbar">
  <div class="wordmark"><span class="sq"></span>BRIDGE ON</div>
  <nav class="nav">
    <span class="active">Home</span><span>About Us</span><span>Services</span><span>Industry Solutions</span><span>Testimonials</span><span>Blog</span><span>Our Company</span><span>Contact Us</span>
  </nav>
</div>
<div class="abs hero-title">BRIDGE ON</div>
<div class="abs hero-text">Lorem ipsum dolor sit amet, consectetur adipiscing elit, sed do eiusmod tempor incididunt ut labore et dolore magna aliqua.</div>
<div class="btn btn-light" style="left:536px;top:432px;width:128px;height:38px">GET STARTED</div>
<div class="round-arrow" style="left:97px;top:340px;width:44px;height:44px;background:#000"><svg width="16" height="16" viewBox="0 0 16 16"><path d="M10 3 5 8l5 5" fill="none" stroke="#fff" stroke-width="2"/></svg></div>
<div class="round-arrow" style="left:1055px;top:340px;width:44px;height:44px;background:#000"><svg width="16" height="16" viewBox="0 0 16 16"><path d="M6 3l5 5-5 5" fill="none" stroke="#fff" stroke-width="2"/></svg></div>

<!-- About -->
<div class="abs about-band"></div>
<h2 class="section-title about-title">About Us</h2>
<p class="abs about-text">Lorem ipsum dolor sit amet, consectetur adipiscing elit, sed do eiusmod tempor incididunt ut labore et dolore magna aliqua. Ut enim ad minim veniam, quis nostrud exercitation ullamco laboris nisi ut aliquip ex ea commodo consequat. Duis aute irure dolor in reprehenderit in voluptate velit esse cillum dolore eu fugiat nulla pariatur. Excepteur sint occaecat cupidatat non proident, sunt in culpa qui officia deserunt mollit anim id est laborum.</p>
<div class="btn btn-light" style="left:141px;top:971px;width:129px;height:37px">LEARN MORE</div>
<div class="photo" style="left:600px;top:735px;width:455px;height:402px;background:linear-gradient(160deg,#c9cdd0,#8d9195 55%,#5e6266)" role="img" aria-label="Meeting around a table with a whiteboard presentation"></div>

<!-- Services -->
<h2 class="section-title" style="left:0;top:1232px;width:1200px;text-align:center">Our Services</h2>
<div class="round-arrow dark-arrow" style="left:50px"><svg width="16" height="16" viewBox="0 0 16 16"><path d="M10 3 5 8l5 5" fill="none" stroke="#fff" stroke-width="2"/></svg></div>
<div class="round-arrow dark-arrow" style="left:1106px"><svg width="16" height="16" viewBox="0 0 16 16"><path d="M6 3l5 5-5 5" fill="none" stroke="#fff" stroke-width="2"/></svg></div>

<div class="service" style="left:144px">
  <svg viewBox="0 0 84 84" fill="none" stroke="#000" stroke-width="3"><path d="M18 40V30a24 24 0 0 1 48 0v10"/><rect x="12" y="38" width="12" height="22" rx="3"/><rect x="60" y="38" width="12" height="22" rx="3"/><path d="M24 44h12c4 0 6 2 6 4 0-2 2-4 6-4h12v28H48c-4 0-6 2-6 4 0-2-2-4-6-4H24z"/><path d="M42 48v28"/></svg>
  Audio &amp; Visual Design
</div>
<div class="service" style="left:378px">
  <svg viewBox="0 0 84 84" fill="none" stroke="#000" stroke-width="3"><path d="M36 8h12l2 9 8 4 8-5 8 8-5 8 4 8 9 2v12l-9 2-4 8 5 8-8 8-8-5-8 4-2 9H36l-2-9-8-4-8 5-8-8 5-8-4-8-9-2V36l9-2 4-8-5-8 8-8 8 5 8-4z"/><circle cx="42" cy="42" r="18"/><path d="M34 48l12-12m-4-4 8 8"/><circle cx="60" cy="62" r="12" fill="#fff"/><path d="M54 62l4 4 8-8"/></svg>
  Install
</div>
<div class="service" style="left:612px">
  <svg viewBox="0 0 84 84" fill="none" stroke="#000" stroke-width="3"><circle cx="16" cy="14" r="6"/><circle cx="68" cy="14" r="6"/><path d="M10 28h12v18l8 6v20M74 28H62v18l-8 6v20"/><path d="M30 52h24M42 52v22"/><rect x="32" y="6" width="20" height="14" rx="2"/><path d="M36 20l-2 6 6-6"/></svg>
  Consulting
</div>
<div class="service" style="left:846px">
  <svg viewBox="0 0 84 84" fill="none" stroke="#000" stroke-width="3"><path d="M32 6h12l2 8 7 3 7-4 8 8-4 7 3 7 8 2v6"/><path d="M28 66l-7 4-8-8 4-7-3-7-8-2V34l8-2 3-7-4-7 8-8 7 4"/><circle cx="38" cy="38" r="16"/><path d="M31 38l5 5 9-9"/><rect x="44" y="52" width="34" height="24" rx="2" fill="#fff"/><path d="M54 52v-5h14v5M44 62h34"/></svg>
  Project Completion
</div>

<!-- Industry -->
<div class="abs industry"></div>
<div class="abs" style="left:53px;top:1579px;width:501px;height:464px;background:var(--black)"></div>
<div class="photo" style="left:144px;top:1673px;width:412px;height:323px;background:linear-gradient(150deg,#e6e8ea,#b7bcc0 50%,#7f8489)" role="img" aria-label="Open-plan office with staff at computer desks"></div>
<h2 class="section-title" style="left:600px;top:1668px">Industry Solutions</h2>
<p class="abs industry-text">Lorem ipsum dolor sit amet, consectetur adipiscing elit, sed do eiusmod tempor incididunt ut labore et dolore magna aliqua. Ut enim ad minim veniam, quis nostrud exercitation ullamco laboris nisi ut aliquip ex ea commodo consequat. Duis aute irure dolor in reprehenderit in voluptate velit esse cillum dolore eu fugiat nulla pariatur. Excepteur sint occaecat cupidatat non proident, sunt in culpa qui officia deserunt mollit anim id est laborum. Lorem ipsum dolor sit amet, consectetur adipiscing elit, sed do eiusmod tempor incididunt ut labore et dolore magna aliqua. Ut enim ad minim veniam, quis nostrud exercitation ullamco laboris nisi ut aliquip ex ea commodo consequat. Duis aute irure dolor in reprehenderit in voluptate velit esse cillum dolore eu fugiat nulla pariatur.</p>
<div class="btn btn-dark" style="left:600px;top:1959px;width:129px;height:36px">LEARN MORE</div>

<!-- Testimonials -->
<div class="photo testi-bg" role="img" aria-label="Dimmed photo of a business meeting"></div>
<h2 class="section-title" style="left:0;top:2185px;width:1200px;text-align:center;color:var(--white)">Testimonials</h2>
<div class="card" style="left:144px">
  <p>Lorem ipsum dolor sit amet, consectetur adipiscing elit, sed do eiusmod tempor incididunt ut labore et dolore magna aliqua. Lorem ipsum dolor sit amet, consectetur adipiscing elit, sed do eiusmod tempor incididunt ut labore et dolore magna aliqua. Lorem ipsum dolor sit amet, consectetur adipiscing elit, sed do eiusmod tempor incididunt ut labore et dolore magna aliqua.</p>
  <div class="who"><div class="avatar" role="img" aria-label="Client portrait"></div><div><div class="name">John Doe</div><div class="co">Company name</div></div></div>
  <svg class="quote" viewBox="0 0 64 48"><path d="M28 8C14 10 6 20 6 32a8 8 0 1 0 16 0 8 8 0 0 0-8-8c2-6 7-10 14-11zM58 8C44 10 36 20 36 32a8 8 0 1 0 16 0 8 8 0 0 0-8-8c2-6 7-10 14-11z" fill="none" stroke="#fff" stroke-width="2.5"/></svg>
</div>
<div class="card" style="left:617px">
  <p>Lorem ipsum dolor sit amet, consectetur adipiscing elit, sed do eiusmod tempor incididunt ut labore et dolore magna aliqua. Lorem ipsum dolor sit amet, consectetur adipiscing elit, sed do eiusmod tempor incididunt ut labore et dolore magna aliqua. Lorem ipsum dolor sit amet, consectetur adipiscing elit, sed do eiusmod tempor incididunt ut labore et dolore magna aliqua.</p>
  <div class="who"><div class="avatar" role="img" aria-label="Client portrait"></div><div><div class="name">John Doe</div><div class="co">Company name</div></div></div>
  <svg class="quote" viewBox="0 0 64 48"><path d="M28 8C14 10 6 20 6 32a8 8 0 1 0 16 0 8 8 0 0 0-8-8c2-6 7-10 14-11zM58 8C44 10 36 20 36 32a8 8 0 1 0 16 0 8 8 0 0 0-8-8c2-6 7-10 14-11z" fill="none" stroke="#fff" stroke-width="2.5"/></svg>
</div>
<div class="abs dots"><span></span><span></span><span></span><span></span></div>

<!-- Our company -->
<h2 class="section-title" style="left:0;top:2716px;width:1200px;text-align:center">Our Company</h2>
<p class="abs company-text">Lorem ipsum dolor sit amet, consectetur adipiscing elit, sed do eiusmod tempor incididunt ut labore et dolore magna aliqua. Ut enim ad minim veniam, quis nostrud exercitation ullamco laboris nisi ut aliquip ex ea commodo consequat. Duis aute irure dolor in reprehenderit in voluptate velit esse cillum dolore eu fugiat nulla pariatur. Excepteur sint occaecat cupidatat non proident, sunt in culpa qui officia deserunt mollit anim id est laborum. Lorem ipsum dolor sit amet, consectetur adipiscing elit, sed do eiusmod tempor incididunt ut labore et dolore magna aliqua.</p>
<div class="btn btn-dark" style="left:536px;top:2888px;width:128px;height:37px">LEARN MORE</div>

<!-- Contact -->
<div class="photo contact-bg" role="img" aria-label="Colleagues working at laptops in an office"></div>
<div class="abs footer-bg"></div>
<div class="abs form-card"></div>
<h2 class="section-title" style="left:228px;top:3241px;width:744px;text-align:center">Get in Touch</h2>
<div class="field" style="left:292px;top:3313px;width:292px">First name</div>
<div class="field" style="left:611px;top:3313px;width:292px">Last name</div>
<div class="field" style="left:292px;top:3377px;width:292px">Email</div>
<div class="field" style="left:611px;top:3377px;width:292px">Phone</div>
<div class="field" style="left:292px;top:3497px;width:611px">Message</div>
<div class="btn btn-dark" style="left:534px;top:3540px;width:127px;height:37px">SUBMIT</div>

<!-- Footer -->
<div class="abs wordmark footer-mark"><span class="sq"></span>BRIDGE ON</div>
<div class="abs rule" style="top:3781px"></div>
<nav class="abs foot-nav"><span>HOME</span><span>ABOUT US</span><span>SERVICES</span><span>INDUSTRY SOLUTIONS</span><span>OUR COMPANY</span><span>CONTACT US</span></nav>
<div class="abs rule" style="top:3837px"></div>

<div class="info" style="left:206px">
  <div class="ico"><svg width="14" height="18" viewBox="0 0 14 18"><path d="M7 0a7 7 0 0 0-7 7c0 5 7 11 7 11s7-6 7-11a7 7 0 0 0-7-7zm0 10a3 3 0 1 1 0-6 3 3 0 0 1 0 6z" fill="#000"/></svg></div>
  <div><h4>ADDRESS :</h4><p>Lorem ipsum dolor<br>sit amet</p></div>
</div>
<div class="info" style="left:510px">
  <div class="ico"><svg width="16" height="12" viewBox="0 0 16 12"><rect width="16" height="12" fill="#000"/><path d="M0 0l8 6 8-6" fill="none" stroke="#fff" stroke-width="1.5"/></svg></div>
  <div><h4>EMAIL :</h4><p>info@companyname.com</p></div>
</div>
<div class="info" style="left:814px">
  <div class="ico"><svg width="16" height="16" viewBox="0 0 16 16"><path d="M3 1l3 3-2 2c1 2 4 5 6 6l2-2 3 3-2 2C7 15 1 9 1 3z" fill="#000"/></svg></div>
  <div><h4>PHONE :</h4><p>+1 888 888 8888</p></div>
</div>
<div class="abs rule" style="top:3968px"></div>
<div class="abs copy">© Copyrights 2024 | All Rights Reserved</div>

</body>
</html>
```